"Outside the Box" Newsletter Design Project-Communications Company

I am looking for an Internal newsletter for a communications company that will be sent to our sales and leadership team.
This newsletter will deliver forecasting, sales results, stack rankings for the sales reps, total team results, corporate updates, success stories and updates from Training/Operations/Sales/Marketing (could be a box for each)I would also need a couple sections with a blank header and box to add info as needed, if something comes up that is not set in stone weekly.
I am looking for a template that looks sharp and professional that i can use every week by just dropping content in, (text and possibly an employee picture) I will need it in a format (possibly word) that the will keep the text in line when I drop it in each week. Once complete I can save to a pdf and would like to have the ability to drop it into the body of an email.

We have a racecar theme that we use when training our sales folks so we would like a little bit of that to the newsletter and also incorporate our color scheme from our company.

I would like four versions of the newsletter..all would match other than the title.
1. Week 1 title - Start your engines
2. Week 2 title - Looking for suggestions
3. Week 3 title - Looking for suggestions
4. Week 4 title - Approaching the finish line, this version would also include an employee spotlight, one seperate section.

If we could include a few pics around racing that would be good, not over the top, just a few to give it a little of that feel. Maybe a checkered flag with the QV logo on it, a racecar..anything else that may make sense.

I will attach our logo and our organization is called SMB (small/medium business) so that should also be placed on there somewhere. Final design would need to be two pages, sharp professional feel, my Vice President likes a very clean look, not too busy. I have also attached a sample newsletter from another group in our company, ours will not have as much content, we are much smaller but this is a sample (on a smaller scale)of what we are looking for. The company look and feel is what we want to follow. Thank you

Target Market(s)

Our Internal sales team.

Industry/Entity Type

Communications

Requirements
Must have
• Ability to update with my content without having things shift and fall out of line..format that will make that easy and then able to save to PDF..2 pages long.
Nice to have
• HTML template to match.

```html
<!DOCTYPE html>
<html lang="en">
<head>
<meta charset="utf-8">
<title>QV Weekly Recap – December 20, 2012</title>
<link rel="stylesheet" href="https://fonts.googleapis.com/css2?family=Open+Sans:wght@400;600;700&display=swap">
<style>
  :root {
    --page-bg: #ececec;
    --card-bg: #ffffff;
    --brand-purple: #7b2a8e;
    --accent-bar: #7e3a93;
    --ink: #333333;
    --ink-soft: #444444;
    --date-purple: #8a2b9c;
    --shadow: rgba(0,0,0,0.12);
  }
  * { box-sizing: border-box; margin: 0; padding: 0; }
  html, body { width: 940px; height: 1200px; overflow: hidden; }
  body {
    background: var(--page-bg);
    font-family: "Open Sans", Verdana, sans-serif;
    color: var(--ink);
    position: relative;
  }
  .masthead { position: absolute; left: 0; top: 0; width: 940px; height: 100px; }
  .brand { position: absolute; left: 30px; top: 12px; display: flex; align-items: center; gap: 8px; }
  .flag { width: 66px; height: 62px; border-radius: 4px;
    background: linear-gradient(135deg, #d8d8d8, #8a8a8a 60%, #c9c9c9); }
  .brand-name { display: flex; align-items: center; gap: 6px; font-weight: 700; font-size: 34px; color: var(--brand-purple); }
  .brand-name .dot { width: 14px; height: 14px; border-radius: 50%; background: var(--brand-purple); }
  .issue { position: absolute; right: 29px; top: 28px; text-align: right; }
  .issue-date { font-size: 18px; font-weight: 700; color: var(--ink); letter-spacing: .2px; }
  .issue-date span { font-weight: 400; }
  .issue-tagline { font-size: 13.5px; margin-top: 3px; color: var(--ink); }

  .card { position: absolute; background: var(--card-bg); box-shadow: 0 1px 3px var(--shadow); overflow: hidden; }
  .section-title { position: relative; font-size: 19.5px; font-weight: 700; color: var(--ink); padding-left: 29px; line-height: 28px; }
  .section-title::before { content: ""; position: absolute; left: 0; top: -6px; width: 6px; height: 44px; background: var(--accent-bar); }
  .body-copy {
    font-size: 13.2px; line-height: 20.5px; color: var(--ink-soft);
    display: -webkit-box; -webkit-box-orient: vertical; overflow: hidden;
  }

  .leaders { left: 29px; top: 105px; width: 882px; height: 148px; }
  .leaders .col { position: absolute; top: 14px; }
  .leaders .vp { left: 0; width: 450px; }
  .leaders .events { left: 470px; width: 412px; }
  .leaders .section-title { display: flex; align-items: center; gap: 10px; padding-left: 29px; }
  .leaders .events .section-title { padding-left: 16px; }
  .leaders .section-title svg { flex: none; }
  .leaders .vp .body-copy { margin: 12px 0 0 29px; width: 414px; -webkit-line-clamp: 4; }
  .event-grid { display: grid; grid-template-columns: 225px 170px; margin: 12px 0 0 0; font-size: 13.2px; line-height: 20.5px; }
  .event-when { color: var(--date-purple); }
  .event-what { color: var(--ink); }

  .feature { left: 29px; top: 266px; width: 882px; height: 384px; }
  .feature-photo { height: 200px; background: linear-gradient(180deg, #6f6a62 0%, #3a3a3a 45%, #8b8b86 75%, #d9d9d6 100%); }
  .feature-title { text-align: center; font-size: 18.5px; font-weight: 700; margin: 14px 0 8px; color: var(--ink); line-height: 26px; }
  .feature .body-copy { margin: 0 29px; -webkit-line-clamp: 6; }

  .update { top: 666px; width: 427px; height: 242px; padding-top: 14px; }
  .update.ops { left: 29px; }
  .update.fin { left: 484px; }
  .update .body-copy { margin: 12px 22px 0 29px; -webkit-line-clamp: 9; }

  .spotlight { left: 29px; top: 922px; width: 882px; height: 256px; }
  .spotlight-text { position: absolute; left: 0; top: 14px; width: 600px; }
  .spotlight .section-title { font-size: 21px; }
  .spotlight .body-copy { margin: 12px 0 0 29px; width: 560px; -webkit-line-clamp: 9; }
  .spotlight-photo { position: absolute; right: 0; top: 0; width: 281px; height: 256px;
    background: linear-gradient(160deg, #cfc3a8 0%, #a89576 40%, #4a4036 100%); }
</style>
</head>
<body>
  <header class="masthead">
    <div class="brand">
      <div class="flag" role="img" aria-label="Crossed checkered racing flags"></div>
      <div class="brand-name"><span class="dot"></span>QV</div>
      <div class="flag" role="img" aria-label="Crossed checkered racing flags"></div>
    </div>
    <div class="issue">
      <div class="issue-date">DECEMBER 20, 2012 <span>ISSUE</span></div>
      <div class="issue-tagline">A Weekly Recap of Important Things Going on QV That You Need To Know</div>
    </div>
  </header>

  <section class="card leaders">
    <div class="col vp">
      <h2 class="section-title">
        <svg width="20" height="20" viewBox="0 0 20 20" aria-hidden="true">
          <circle cx="10" cy="6" r="4.5" fill="#e0a96d"/>
          <path d="M2 19c0-5 3.5-7.5 8-7.5s8 2.5 8 7.5z" fill="#3b6ea8"/>
        </svg>
        Vice President Messages
      </h2>
      <p class="body-copy">A wonderful serenity has taken possession of my entire soul, like these sweet mornings of spring which I enjoy with my whole heart. I am alone, and feel the charm of existence in this spot, which was created for the bliss of souls like mine. I</p>
    </div>
    <div class="col events">
      <h2 class="section-title">
        <svg width="20" height="20" viewBox="0 0 20 20" aria-hidden="true">
          <rect x="1.5" y="2.5" width="17" height="16" rx="1.5" fill="#fff" stroke="#6b5a8e" stroke-width="1.5"/>
          <rect x="1.5" y="2.5" width="17" height="4.5" fill="#8a6bb0"/>
          <g fill="#8a6bb0"><rect x="4" y="9" width="3" height="2.5"/><rect x="8.5" y="9" width="3" height="2.5"/><rect x="13" y="9" width="3" height="2.5"/><rect x="4" y="13" width="3" height="2.5"/><rect x="8.5" y="13" width="3" height="2.5"/></g>
        </svg>
        Upcoming Event
      </h2>
      <div class="event-grid">
        <div class="event-when">Mon, July 23</div><div class="event-when">June 1—August 31</div>
        <div class="event-what">CR Q2 Presentation @3 pm</div><div class="event-what">Double Down Challenge</div>
        <div class="event-when">Fri, August 3</div><div class="event-when">June 1—August 31</div>
        <div class="event-what">Chicago Mid-Year Town</div><div class="event-what">CR TooHot To Handle</div>
      </div>
    </div>
  </section>

  <section class="card feature">
    <div class="feature-photo" role="img" aria-label="Race car crossing the finish line on a track"></div>
    <h2 class="feature-title">WEEK 4 - Crossing the finish line in July</h2>
    <p class="body-copy">Lorem ipsum dolor sit amet, consectetuer adipiscing elit. Aenean commodo ligula eget dolor. Aenean massa. Cum sociis natoque penatibus et magnis dis parturient montes, nascetur ridiculus mus. Donec quam felis, ultricies nec, pellentesque eu, pretium quis, sem. Nulla consequat massa quis enim. Donec pede justo, fringilla vel, aliquet nec, vulputate eget, arcu. In enim justo, rhoncus ut, imperdiet a, venenatis vitae, justo. Nullam dictum felis eu pede mollis pretium. Integer tincidunt. Cras dapibus. Vivamus elementum semper nisi. Aenean vulputate eleifend tellus. Aenean leo ligula, porttitor eu, consequat vitae, eleifend ac, enim. Aliquam lorem ante, dapibus in, viverra quis, feugiat a, tellus. Phasellus viverra nulla ut</p>
  </section>

  <section class="card update ops">
    <h2 class="section-title">Updates from Operations</h2>
    <p class="body-copy">Far far away, behind the word mountains, far from the countries Vokalia and Consonantia, there live the blind texts. Separated they live in Bookmarksgrove right at the coast of the Semantics, a large language ocean. A small river named Duden flows by their place and supplies it with the necessary regelialia. It is a paradisematic country, in which roasted parts of sentences fly into your mouth. Even the all-powerful Pointing has no control about the blind texts it is an almost</p>
  </section>

  <section class="card update fin">
    <h2 class="section-title">Updates from Financial</h2>
    <p class="body-copy">Far far away, behind the word mountains, far from the countries Vokalia and Consonantia, there live the blind texts. Separated they live in Bookmarksgrove right at the coast of the Semantics, a large language ocean. A small river named Duden flows by their place and supplies it with the necessary regelialia. It is a paradisematic country, in which roasted parts of sentences fly into your mouth. Even the all-powerful Pointing has no control about the blind texts it is an almost</p>
  </section>

  <section class="card spotlight">
    <div class="spotlight-text">
      <h2 class="section-title">Say Hello to Daniel Brooks from England.</h2>
      <p class="body-copy">Lorem ipsum dolor sit amet, consectetuer adipiscing elit. Aenean commodo ligula eget dolor. Aenean massa. Cum sociis natoque penatibus et magnis dis parturient montes, nascetur ridiculus mus. Donec quam felis, ultricies nec, pellentesque eu, pretium quis, sem. Nulla consequat massa quis enim. Donec pede justo, fringilla vel, aliquet nec, vulputate eget, arcu. In enim justo, rhoncus ut, imperdiet a, venenatis vitae, justo. Nullam dictum felis eu pede mollis pretium. Integer tincidunt. Cras dapibus. Vivamus elementum semper nisi. Aenean vulputate eleifend tellus. Aenean leo ligula, porttitor eu, consequat vitae, eleifend ac, enim. Aliquam lorem ante, dapibus in, viverra quis, feugiat a, tellus. Phasellus viverra nulla ut</p>
    </div>
    <div class="spotlight-photo" role="img" aria-label="Employee spotlight portrait photo"></div>
  </section>
</body>
</html>
```